Set up small scale company website

We need a website set up for our educational consultancy - Vexmore Education. We like the following site and want something similar www.plindarhub.co.uk We can provide the copy and images but need the following:- setting up the overall theme and design - to our requirements on colours and forma- Approximately 4 pages of services offered and with an index pageEtct (yellow and green)And the following pages - as well as a home page:- A contact page linked to our email addresses and registered business address 17 Wexbury Lane, Harwich, Essex, CO14 8PN- About Us page - An index of services page that links to between 4-6 pages outlining services- A News page that links to updates of latest services, events and activities - easily updated by usOn the homepage we'd like links to chirpnet and WorkLoop feeds and links to our other blogs and websites
Target Market(s)
Schools, local authoroties and multi-academy trusts
Logo Text
Vexmore Education
Coding
Coded - Design and coding required
Number of Pages Required
5+ page
Font styles to use
Requirements
Should not have
- No tacky pictures of mortar boards or chalk boards etc.

```html
<!DOCTYPE html>
<html lang="en">
<head>
<meta charset="utf-8">
<title>Vexmore Education</title>
<link rel="stylesheet" href="https://fonts.googleapis.com/css2?family=Montserrat:wght@400;600;700&family=Roboto:wght@300;400;500;700&display=swap">
<style>
:root{
  --green:#8cc63f;
  --green-dark:#7ab52e;
  --yellow:#f3e41d;
  --ink:#222;
  --text:#444;
  --muted:#888;
  --panel:#efefef;
  --band:#f2f2f2;
  --footer:#2a2a2a;
  --white:#fff;
  --blue:#1d8bd6;
}
*{box-sizing:border-box;margin:0;padding:0}
html,body{width:1200px;height:3315px;overflow:hidden}
body{position:relative;background:var(--white);font-family:'Roboto',sans-serif;color:var(--text)}
.abs{position:absolute}

/* header */
.brand{left:121px;top:60px;display:flex;align-items:center;gap:12px}
.brand-mark{width:34px;height:34px;background:var(--green)}
.brand-name{font-family:'Roboto',sans-serif;font-weight:700;font-size:34px;color:var(--ink)}
.topline{left:464px;top:30px;width:634px;text-align:right;font-size:15px;color:var(--muted)}
.topline span{margin-left:18px}
.header-rule{left:464px;top:69px;width:634px;height:1px;background:#e6e6e6}
.nav{right:102px;top:84px;display:flex;gap:0;align-items:center}
.nav a{font-size:15px;color:#777;text-decoration:none;text-transform:uppercase;margin-left:30px}
.nav a.active{background:var(--green);color:var(--white);font-weight:700;padding:7px 14px;margin-left:0;margin-right:18px}

/* hero */
.hero{left:0;top:140px;width:1200px;height:479px;background:linear-gradient(120deg,#3b3a36 0%,#6a6258 35%,#2f2c2a 65%,#574a40 100%)}
.hero-shade{left:0;top:140px;width:1200px;height:479px;background:rgba(20,20,20,.45)}
.hero-kicker{left:0;top:285px;width:1200px;text-align:center;font-family:'Montserrat',sans-serif;font-size:32px;color:var(--white)}
.hero-title{left:0;top:328px;width:1200px;text-align:center;font-family:'Montserrat',sans-serif;font-weight:600;font-size:64px;color:var(--white)}
.btn{display:inline-block;background:var(--green);color:var(--white);font-weight:700;text-transform:uppercase;text-align:center}
.hero-btn{left:538px;top:445px;width:124px;height:32px;line-height:32px;font-size:12px}
.hero-dots{left:1146px;top:296px;display:flex;flex-direction:column;gap:18px}
.hero-dots i{display:block;width:6px;height:6px;border-radius:50%;background:rgba(255,255,255,.4)}
.hero-dots i:first-child{background:var(--white)}

/* tabs */
.tabs{left:119px;top:718px;display:flex}
.tab{width:208px;height:51px;line-height:51px;text-align:center;font-family:'Montserrat',sans-serif;font-weight:600;font-size:19px;color:var(--white);background:var(--green);text-transform:uppercase}
.tab.mid{background:var(--yellow);color:#b9b21a;width:200px}
.tab.end{width:208px}
.panel{left:119px;top:769px;width:977px;height:398px;background:var(--panel)}
.panel-title{left:171px;top:797px;font-size:22px;font-weight:500;color:var(--ink);text-transform:uppercase}
.panel-text{left:171px;top:874px;width:500px;font-size:21px;line-height:31px;color:#555;font-weight:300}
.panel-photo{left:727px;top:831px;width:325px;height:278px;background:linear-gradient(160deg,#d9d4c8,#a59a8b 60%,#6e625a)}

/* section titles */
.ghost{left:0;width:1200px;text-align:center;font-family:'Montserrat',sans-serif;font-weight:700;font-size:46px;color:#f3f3f3;text-transform:uppercase}
.sec-title{left:0;width:1200px;text-align:center;font-family:'Montserrat',sans-serif;font-weight:700;font-size:31px;color:var(--green);text-transform:uppercase}

/* social cards */
.card{background:var(--white);box-shadow:0 3px 10px rgba(0,0,0,.18)}
.tweet{top:1357px;width:228px;height:331px;padding:12px 10px}
.tw-head{display:flex;align-items:center;gap:8px;height:30px}
.tw-ava{width:28px;height:28px;border-radius:50%;border:1px solid #ddd;background:#f6f6f6}
.tw-name{font-size:11px;font-weight:700;color:var(--ink)}
.tw-handle{font-size:9px;color:var(--muted)}
.tw-text{margin-top:12px;font-size:11.5px;line-height:14px;color:#333}
.tw-text b{color:var(--blue);font-weight:400}
.tw-photo{margin-top:6px;height:124px;background:linear-gradient(135deg,#c7b9a4,#8f7d66 60%,#e0d8cc)}
.tw-meta{margin-top:8px;font-size:8px;color:var(--muted);border-bottom:1px solid #eee;padding-bottom:8px}
.tw-stats{margin-top:8px;font-size:8px;color:#333;border-bottom:1px solid #eee;padding-bottom:8px}
.tw-actions{margin-top:8px;display:flex;justify-content:space-around}
.feature{left:747px;top:1355px;width:307px;height:334px;background:#f3f3f3}
.feature-photo{height:154px;background:linear-gradient(120deg,#5b6b7a,#c9ced4 50%,#3d4650)}
.feature-badge{left:0;top:0;width:50px;height:50px;background:#1a7ab8}
.feature-body{padding:32px 16px}
.feature-kicker{font-size:9px;color:var(--muted);text-transform:uppercase}
.feature-title{margin-top:10px;font-size:14px;font-weight:700;color:var(--ink);text-transform:uppercase}
.feature-text{margin-top:10px;font-size:10.5px;line-height:15px;color:var(--muted)}
.feature-link{margin-top:24px;font-size:8px;color:var(--blue);text-transform:uppercase}

/* news */
.news{left:0;top:1761px;width:1200px;height:367px;background:var(--band)}
.news-ghost{left:285px;top:1822px;font-family:'Montserrat',sans-serif;font-weight:700;font-size:70px;color:#ddd}
.news-title{left:232px;top:1820px;font-family:'Montserrat',sans-serif;font-weight:700;font-size:40px;line-height:46px;color:var(--green);text-transform:uppercase}
.news-text{left:234px;top:1953px;width:290px;font-size:13px;line-height:19px;color:#222}
.news-btn{left:234px;top:2006px;width:90px;height:24px;line-height:24px;font-size:10px}
.news-photo{left:599px;top:1808px;width:369px;height:188px;background:linear-gradient(110deg,#3e4442,#8a7a6c 45%,#b78a6a 70%,#5c4a42)}
.news-quote{left:652px;top:1947px;width:316px;height:115px;background:linear-gradient(100deg,var(--green),var(--yellow));padding:14px 22px;box-shadow:0 3px 8px rgba(0,0,0,.15)}
.news-quote p{font-size:11.5px;line-height:15px;font-weight:700;color:#222}
.news-quote small{display:block;margin-top:12px;font-size:11.5px;font-weight:700;color:#222}

/* testimonials */
.testi{top:2338px;width:393px;height:186px;border:1px solid #bdbdbd;background:var(--white);text-align:center;padding:66px 30px 0}
.testi-ava{top:2300px;width:92px;height:92px;border-radius:50%;background:var(--green);padding:5px}
.testi-ava div{width:100%;height:100%;border-radius:50%;background:linear-gradient(160deg,#b7aa9b,#6a5c50)}
.testi p{font-size:15px;line-height:19px;color:#8a8a8a;font-weight:300}
.testi strong{display:block;margin-top:12px;font-size:16px;font-weight:400;color:#333}
.quote-mark{font-family:'Montserrat',sans-serif;font-weight:700;font-size:50px;color:var(--green);line-height:1}

/* contact */
.contact{left:0;top:2617px;width:1200px;height:411px;background:linear-gradient(100deg,#8cc63f 0%,#b3d632 45%,#f3e41d 100%)}
.contact-ghost{left:0;top:2640px;width:1200px;text-align:center;font-family:'Montserrat',sans-serif;font-weight:700;font-size:44px;color:rgba(255,255,255,.18)}
.contact-title{left:0;top:2662px;width:1200px;text-align:center;font-family:'Montserrat',sans-serif;font-weight:700;font-size:31px;color:var(--white)}
.contact-sub{left:0;top:2721px;width:1200px;text-align:center;font-size:9px;color:#5b7a1d}
.field{left:252px;width:327px;height:22px;background:var(--white);font-size:9px;color:#aaa;padding:5px 8px}
.field.area{left:619px;width:329px;height:100px}
.send{left:544px;top:2922px;width:115px;height:32px;line-height:32px;font-size:11px;background:var(--green-dark)}

/* footer */
.footer{left:0;top:3028px;width:1200px;height:287px;background:var(--footer)}
.f-brand{left:121px;top:3094px;display:flex;align-items:center;gap:10px}
.f-brand .brand-mark{background:var(--white)}
.f-brand .brand-name{color:var(--white);font-size:32px}
.f-addr{left:127px;top:3164px;font-size:11px;line-height:20px;color:#ddd}
.f-col{top:3057px}
.f-col h4{font-size:12px;letter-spacing:1.5px;color:var(--white);font-weight:700;text-transform:uppercase;margin-bottom:16px}
.f-col li{list-style:none;font-size:10px;color:#ddd;height:23px}
.f-col li i{display:inline-block;width:18px;height:18px;border-radius:50%;background:#3b5b9b;vertical-align:middle;margin-right:8px}
.f-col li i.b{background:var(--blue)}
.f-col li i.c{background:#1a7ab8}
.f-col.social li{height:34px}
.f-rule{left:121px;top:3231px;width:973px;height:1px;background:#555}
.f-copy{left:0;top:3265px;width:1200px;text-align:center;font-size:10px;color:#ccc}
</style>
</head>
<body>

<!-- header -->
<div class="abs brand"><div class="brand-mark"></div><div class="brand-name">Vexmore Education</div></div>
<div class="abs topline"><span>&#9742; 777-40-515</span><span>&#9993; info@vexmore.edu</span></div>
<div class="abs header-rule"></div>
<nav class="abs nav"><a class="active" href="#">Home</a><a href="#">Services</a><a href="#">News</a><a href="#">About Us</a><a href="#">Contact Us</a></nav>

<!-- hero -->
<div class="abs hero" role="img" aria-label="Group of students working together around a table"></div>
<div class="abs hero-shade"></div>
<div class="abs hero-kicker">WELCOME TO</div>
<div class="abs hero-title">VEXMORE EDUCATION</div>
<div class="abs btn hero-btn">Learn More</div>
<div class="abs hero-dots"><i></i><i></i><i></i><i></i></div>

<!-- about tabs -->
<div class="abs tabs"><div class="tab">About Us</div><div class="tab mid">How It Works</div><div class="tab end">Benefits</div></div>
<div class="abs panel"></div>
<div class="abs panel-title">Welcome to Vexmore Education</div>
<p class="abs panel-text">Sed ut perspiciatis unde omnis iste natus error sit voluptatem accusantium doloremque laudantium, totam rem aperiam, eaque ipsa quae ab illo inventore veritatis et quasi architecto beatae vitae dicta sunt explicabo.</p>
<div class="abs panel-photo" role="img" aria-label="Young woman thinking in front of a wall of sketched ideas"></div>

<!-- social feeds -->
<div class="abs ghost" style="top:1222px">Our Social Feeds</div>
<div class="abs sec-title" style="top:1247px">Our Social Feeds</div>

<div class="abs card tweet" style="left:170px">
  <div class="tw-head"><div class="tw-ava"></div><div><div class="tw-name">Vexmore Education</div><div class="tw-handle">@vexmoreedu</div></div></div>
  <p class="tw-text">Lorem Ipsum is simply dummy text of the printing and typesetting industry. Lorem when an unknown printer took a galley of <b>#vexmoreedu</b></p>
  <div class="tw-photo" role="img" aria-label="Hand placing a wooden block on a stacked tower"></div>
  <div class="tw-meta">5:11 PM - 08 Feb 17</div>
  <div class="tw-stats"><b>133</b> RETWEETS &nbsp; <b>1,176</b> LIKES</div>
  <div class="tw-actions">
    <svg width="14" height="12" viewBox="0 0 14 12"><path d="M6 1 1 6l5 5M1 6h8a4 4 0 0 1 4 4" fill="none" stroke="#777" stroke-width="1.6"/></svg>
    <svg width="16" height="12" viewBox="0 0 16 12"><path d="M3 10V2h8M13 2v8H5" fill="none" stroke="#777" stroke-width="1.6"/></svg>
    <svg width="14" height="12" viewBox="0 0 14 12"><path d="M7 11 1.5 5.5a3 3 0 0 1 5.5-3 3 3 0 0 1 5.5 3z" fill="#777"/></svg>
    <svg width="14" height="12" viewBox="0 0 14 12"><rect x="1" y="2" width="12" height="8" fill="none" stroke="#777" stroke-width="1.6"/><path d="M1 2l6 5 6-5" fill="none" stroke="#777" stroke-width="1.4"/></svg>
  </div>
</div>

<div class="abs card tweet" style="left:460px">
  <div class="tw-head"><div class="tw-ava"></div><div><div class="tw-name">Vexmore Education</div><div class="tw-handle">@vexmoreedu</div></div></div>
  <p class="tw-text">Lorem Ipsum is simply dummy text of the printing and typesetting industry. Lorem when an unknown printer took a galley of <b>#vexmoreedu</b></p>
  <div class="tw-photo" role="img" aria-label="Hand placing a wooden block on a stacked tower"></div>
  <div class="tw-meta">5:11 PM - 08 Feb 17</div>
  <div class="tw-stats"><b>133</b> RETWEETS &nbsp; <b>1,176</b> LIKES</div>
  <div class="tw-actions">
    <svg width="14" height="12" viewBox="0 0 14 12"><path d="M6 1 1 6l5 5M1 6h8a4 4 0 0 1 4 4" fill="none" stroke="#777" stroke-width="1.6"/></svg>
    <svg width="16" height="12" viewBox="0 0 16 12"><path d="M3 10V2h8M13 2v8H5" fill="none" stroke="#777" stroke-width="1.6"/></svg>
    <svg width="14" height="12" viewBox="0 0 14 12"><path d="M7 11 1.5 5.5a3 3 0 0 1 5.5-3 3 3 0 0 1 5.5 3z" fill="#777"/></svg>
    <svg width="14" height="12" viewBox="0 0 14 12"><rect x="1" y="2" width="12" height="8" fill="none" stroke="#777" stroke-width="1.6"/><path d="M1 2l6 5 6-5" fill="none" stroke="#777" stroke-width="1.4"/></svg>
  </div>
</div>

<div class="abs card feature">
  <div class="feature-photo" role="img" aria-label="Students working on laptops in a shared workspace"></div>
  <div class="abs feature-badge"></div>
  <div class="feature-body">
    <div class="feature-kicker">Internet Marketing</div>
    <div class="feature-title">Duis vulputate odio, vel pretium</div>
    <p class="feature-text">Morbi porttitor in purus et viverra. Nulla auctor semper mauris an amet dapibus. Donec velit quam, molestie.</p>
    <div class="feature-link">Read More</div>
  </div>
</div>

<!-- news -->
<div class="abs news"></div>
<div class="abs news-ghost">NEWS</div>
<div class="abs news-title">Read<br>Our News</div>
<p class="abs news-text">We work as one team with our clients in an iterative design and development process.</p>
<div class="abs btn news-btn">View All</div>
<div class="abs news-photo" role="img" aria-label="Smiling woman with glasses working beside a brick wall"></div>
<div class="abs news-quote">
  <p>My mission in life is not merely to survive, but to thrive; and to do so with some passion, some compassion, some humor, and some style.</p>
  <small>&mdash;&nbsp; Published on 18 March 2018</small>
</div>

<!-- testimonials -->
<div class="abs ghost" style="top:2162px">Testimonials</div>
<div class="abs sec-title" style="top:2187px">Testimonials</div>

<svg class="abs" style="left:158px;top:2412px" width="20" height="32" viewBox="0 0 20 32"><path d="M17 2 3 16l14 14" fill="none" stroke="#999" stroke-width="3"/></svg>
<svg class="abs" style="left:1022px;top:2412px" width="20" height="32" viewBox="0 0 20 32"><path d="M3 2l14 14L3 30" fill="none" stroke="#999" stroke-width="3"/></svg>

<div class="abs testi" style="left:205px">
  <p><span class="quote-mark" style="float:left;margin:-4px 6px 0 -8px">&ldquo;</span>Class aptent taciti sociosqu ad litora torquent per conubia nostra per inceptos hymenaeos Proin nulla arcu nonummy luctus<span class="quote-mark" style="vertical-align:-18px;margin-left:4px">&rdquo;</span></p>
  <strong>By Author Name</strong>
</div>
<div class="abs testi-ava" style="left:356px"><div role="img" aria-label="Portrait of a client"></div></div>

<div class="abs testi" style="left:610px">
  <p><span class="quote-mark" style="float:left;margin:-4px 6px 0 -8px">&ldquo;</span>Class aptent taciti sociosqu ad litora torquent per conubia nostra per inceptos hymenaeos Proin nulla arcu nonummy luctus<span class="quote-mark" style="vertical-align:-18px;margin-left:4px">&rdquo;</span></p>
  <strong>By Author Name</strong>
</div>
<div class="abs testi-ava" style="left:761px"><div role="img" aria-label="Portrait of a client"></div></div>

<!-- contact -->
<div class="abs contact"></div>
<div class="abs contact-ghost">CONTACT</div>
<div class="abs contact-title">CONTACT</div>
<div class="abs contact-sub">Lorem ipsum dolor sit amet consectetur adipiscing elit</div>
<div class="abs field" style="top:2780px">Name</div>
<div class="abs field" style="top:2818px">Email</div>
<div class="abs field" style="top:2856px">Subject</div>
<div class="abs field area" style="top:2780px">Message</div>
<div class="abs btn send">Send Message</div>

<!-- footer -->
<div class="abs footer"></div>
<div class="abs f-brand"><div class="brand-mark"></div><div class="brand-name">Vexmore Education</div></div>
<div class="abs f-addr">Mr. Alan Pressick,<br>17 Wexbury Lane, Harwich, Essex, CO14 8PN</div>
<div class="abs f-col" style="left:491px"><h4>Services</h4><ul><li>Education</li><li>Abroad Education</li><li>Higher Education</li><li>Free Education</li></ul></div>
<div class="abs f-col" style="left:670px"><h4>Links</h4><ul><li>Home</li><li>About us</li><li>Services</li><li>Contact</li></ul></div>
<div class="abs f-col social" style="left:813px"><h4>Connect With Us</h4><ul><li><i></i>Facelane</li><li><i class="b"></i>Chirpnet</li><li><i class="c"></i>WorkLoop</li></ul></div>
<div class="abs f-rule"></div>
<div class="abs f-copy">Copyrights 2019. All rights reserved</div>

</body>
</html>
```